Visit card

Industry/Entity Type

Health Care

Contact Information for Business Card

O VITALIS SYSTEMS
Odile Brevard - chef de Projet

Requirements
Must have
• 318 Gaston Lemaire Street 59710 BÉTHUNE Tel: 33 (0) 327 481 605 Mobile: 06 42 19 37 64 Web: www.quorvexsystems.example Contact: o.brevard@o-vitalissystems.example
Should not have
• Respect for color

```html
<!DOCTYPE html>
<html lang="fr">
<head>
<meta charset="utf-8">
<title>O Vitalis Systems – Business Card</title>
<link href="https://fonts.googleapis.com/css2?family=Lato:wght@400;700;900&display=swap" rel="stylesheet">
<style>
  :root {
    --stage: #161616;
    --card: #1f1f1f;
    --pattern-dark: #242424;
    --pattern-light: #4a4a4a;
    --red: #e2232e;
    --white: #ffffff;
    --text: #e9e9e9;
    --rule: #cfcfcf;
  }
  * { box-sizing: border-box; margin: 0; padding: 0; }
  html, body {
    width: 1200px; height: 900px; overflow: hidden;
    background: var(--stage);
    font-family: "Lato", sans-serif;
  }
  .stage { position: relative; width: 1200px; height: 900px; }
  .card {
    position: absolute; left: 250px; width: 700px; height: 400px;
    background: var(--card);
    box-shadow: 0 18px 40px rgba(0,0,0,.6);
    overflow: hidden;
  }
  .card--back { top: 35px; }
  .card--front { top: 465px; }

  .card__pattern {
    position: absolute; inset: 0;
    background: linear-gradient(100deg, var(--pattern-dark) 0%, var(--pattern-dark) 30%, var(--pattern-light) 100%);
    opacity: .55;
  }

  .brand { position: absolute; display: flex; align-items: center; }
  .brand__dot {
    border-radius: 50%; background: var(--red);
    border: solid var(--white);
    flex-shrink: 0;
  }
  .brand__name {
    color: var(--white); font-weight: 900; line-height: 1.05;
    white-space: nowrap; letter-spacing: .5px;
  }
  .card--back .brand { left: 80px; top: 168px; gap: 16px; }
  .card--back .brand__dot { width: 62px; height: 62px; border-width: 7px; }
  .card--back .brand__name { font-size: 26px; }

  .card--front .brand { left: 40px; top: 150px; gap: 20px; }
  .card--front .brand__dot { width: 100px; height: 100px; border-width: 11px; }
  .card--front .brand__name { font-size: 32px; }

  .divider {
    position: absolute; left: 350px; top: 85px; width: 2px; height: 225px;
    background: var(--rule);
  }
  .contact { position: absolute; left: 376px; top: 82px; color: var(--text); }
  .contact__name {
    color: var(--red); font-weight: 700; font-size: 26px;
    text-transform: uppercase; letter-spacing: .3px;
  }
  .contact__role { font-size: 16px; margin-top: 2px; }
  .contact__address { font-size: 16px; line-height: 1.3; margin-top: 14px; }
  .contact__list { list-style: none; margin-top: 12px; font-size: 16px; line-height: 1.6; }
  .contact__list li { display: flex; align-items: center; gap: 10px; white-space: nowrap; }
  .contact__list svg { width: 14px; height: 14px; flex-shrink: 0; }
</style>
</head>
<body>
<main class="stage">

  <section class="card card--back">
    <div class="card__pattern" role="img" aria-label="Repeating embossed brand mark pattern in dark grey tones"></div>
    <div class="brand">
      <span class="brand__dot"></span>
      <span class="brand__name">O VITALIS<br>SYSTEMS</span>
    </div>
  </section>

  <section class="card card--front">
    <div class="brand">
      <span class="brand__dot"></span>
      <span class="brand__name">O VITALIS<br>SYSTEMS</span>
    </div>
    <div class="divider"></div>
    <div class="contact">
      <h1 class="contact__name">Odile Brevard</h1>
      <p class="contact__role">Chef de Projet</p>
      <p class="contact__address">318 Gaston Lemaire Street<br>59710 BÉTHUNE</p>
      <ul class="contact__list">
        <li>
          <svg viewBox="0 0 16 16" fill="var(--red)"><path d="M3.6 1.2 5.8 3.4 4.6 5.6c.9 2.2 3.2 4.7 5.8 5.8l2.2-1.2 2.2 2.2-1.6 2.2C7.6 14.6 1.4 8.4.9 2.8z"/></svg>
          +33 (0) 327 481 605
        </li>
        <li>
          <svg viewBox="0 0 16 16" fill="none" stroke="var(--red)" stroke-width="1.6"><rect x="4" y="1" width="8" height="14" rx="1.5"/><line x1="7" y1="12.5" x2="9" y2="12.5"/></svg>
          06 42 19 37 64
        </li>
        <li>
          <svg viewBox="0 0 16 16" fill="none" stroke="var(--red)" stroke-width="1.3"><circle cx="8" cy="8" r="6.5"/><ellipse cx="8" cy="8" rx="2.8" ry="6.5"/><line x1="1.5" y1="8" x2="14.5" y2="8"/></svg>
          www.quorvexsystems.example
        </li>
        <li>
          <svg viewBox="0 0 16 16" fill="none" stroke="var(--red)" stroke-width="1.4"><rect x="1" y="3" width="14" height="10" rx="1"/><polyline points="1.5,3.5 8,9 14.5,3.5"/></svg>
          o.brevard@o-vitalissystems.example
        </li>
      </ul>
    </div>
  </section>

</main>
</body>
</html>
```